Personal training and nutrition business needs business card design

We need a business card that outlays our services and invites potential customers to join our team and take the first step to a healthier and more enjoyable life. We cater for any level of fitness and specialize in weight loss and conditioning, strength training, muscle gain and strength endurance. Whether you are just starting off or need some help getting to the next level of your journey we are here to get the job done.
We specialize in one on one or one on two personal training sessions and each program will be custom made to suit individual fitness goals of our clients

```html
<!DOCTYPE html>
<html lang="en">
<head>
<meta charset="utf-8">
<title>Stride &amp; Core — Business Card</title>
<link rel="stylesheet" href="https://fonts.googleapis.com/css2?family=Montserrat:wght@800&family=Oswald:wght@500&family=Comfortaa:wght@700&family=Arimo:wght@400&display=swap">
<style>
  :root {
    --backdrop: #2a2a2c;
    --card-dark: #050505;
    --card-light: #ffffff;
    --ink: #111111;
    --ink-light: #ffffff;
    --purple: #7a3fb8;
    --orchid: #b35ec4;
    --lilac-faint: #ece0f2;
    --muted: #555555;
  }
  * { box-sizing: border-box; margin: 0; padding: 0; }
  html, body { width: 1200px; height: 900px; overflow: hidden; }
  body {
    background: var(--backdrop);
    display: flex;
    flex-direction: column;
    align-items: center;
    justify-content: center;
    gap: 30px;
  }
  .card {
    width: 700px;
    height: 400px;
    position: relative;
    overflow: hidden;
    box-shadow: 0 10px 30px rgba(0,0,0,.45);
  }

  /* Front */
  .card--front {
    background: var(--card-dark);
    display: flex;
    flex-direction: column;
    align-items: center;
    justify-content: center;
  }
  .brand-mark {
    display: flex;
    align-items: center;
    gap: 14px;
  }
  .brand-square {
    width: 26px;
    height: 26px;
    background: var(--purple);
  }
  .brand-name {
    font-family: "Montserrat", sans-serif;
    font-weight: 800;
    font-size: 40px;
    letter-spacing: 1px;
    text-transform: uppercase;
  }
  .card--front .brand-name { color: var(--ink-light); }
  .tagline {
    font-family: "Oswald", sans-serif;
    font-weight: 500;
    color: var(--orchid);
    text-transform: uppercase;
    letter-spacing: 1.5px;
  }
  .card--front .tagline { font-size: 13px; margin-top: 10px; }

  /* Back */
  .card--back { background: var(--card-light); }
  .card--back .brand-block {
    position: absolute;
    left: 50px;
    top: 46px;
  }
  .card--back .brand-name { color: var(--ink); font-size: 42px; line-height: 1.05; }
  .card--back .tagline { font-size: 16px; margin-top: 10px; }

  .holder {
    position: absolute;
    right: 56px;
    top: 56px;
    text-align: right;
  }
  .holder-name {
    font-family: "Comfortaa", sans-serif;
    font-weight: 700;
    font-size: 24px;
    color: var(--purple);
  }
  .holder-role {
    font-family: "Arimo", sans-serif;
    font-size: 13px;
    color: var(--muted);
    margin-top: 4px;
  }

  .contact-list {
    position: absolute;
    left: 50px;
    bottom: 40px;
    list-style: none;
    font-family: "Arimo", sans-serif;
    font-size: 18px;
    color: var(--ink);
  }
  .contact-item {
    display: flex;
    align-items: flex-start;
    gap: 14px;
    line-height: 1.35;
  }
  .contact-item--address { margin-bottom: 18px; }
  .contact-icon {
    width: 18px;
    height: 18px;
    flex: none;
    margin-top: 3px;
    fill: var(--purple);
  }
  .decor-square {
    position: absolute;
    right: 40px;
    bottom: 40px;
    width: 200px;
    height: 200px;
    background: var(--lilac-faint);
  }
</style>
</head>
<body>

  <section class="card card--front">
    <div class="brand-mark">
      <span class="brand-square"></span>
      <span class="brand-name">Stride &amp; Core</span>
    </div>
    <p class="tagline">Personal Training.&nbsp; Nutrition. Motivation</p>
  </section>

  <section class="card card--back">
    <div class="brand-block">
      <p class="brand-name">Stride<br>&amp; Core</p>
      <p class="tagline">Personal Training.&nbsp; Nutrition. Motivation</p>
    </div>

    <div class="holder">
      <p class="holder-name">Marco Delane</p>
      <p class="holder-role">Director</p>
    </div>

    <div class="decor-square"></div>

    <ul class="contact-list">
      <li class="contact-item contact-item--address">
        <svg class="contact-icon" viewBox="0 0 24 24"><path d="M12 2a7 7 0 0 0-7 7c0 5 7 13 7 13s7-8 7-13a7 7 0 0 0-7-7zm0 9.5A2.5 2.5 0 1 1 12 6.5a2.5 2.5 0 0 1 0 5z"/></svg>
        <span>Harbor Point Plaza,<br>Clearwater, Florida 33760</span>
      </li>
      <li class="contact-item">
        <svg class="contact-icon" viewBox="0 0 24 24"><path d="M6.6 10.8a15 15 0 0 0 6.6 6.6l2.2-2.2a1 1 0 0 1 1-.25 11.4 11.4 0 0 0 3.6.57 1 1 0 0 1 1 1V20a1 1 0 0 1-1 1A17 17 0 0 1 3 4a1 1 0 0 1 1-1h3.5a1 1 0 0 1 1 1c0 1.25.2 2.45.57 3.57a1 1 0 0 1-.25 1z"/></svg>
        <span>012 555 0147</span>
      </li>
      <li class="contact-item">
        <svg class="contact-icon" viewBox="0 0 24 24"><path d="M3 5h18v14H3zm2 2v.5l7 4.5 7-4.5V7z"/></svg>
        <span>info@strideandcore.com</span>
      </li>
      <li class="contact-item">
        <svg class="contact-icon" viewBox="0 0 24 24"><path d="M12 2a10 10 0 1 0 0 20 10 10 0 0 0 0-20zm6.9 9h-3a15 15 0 0 0-1.3-5.6A8 8 0 0 1 18.9 11zM12 4.1c.9 1.2 1.8 3.6 1.9 6.9h-3.8c.1-3.3 1-5.7 1.9-6.9zM9.4 5.4A15 15 0 0 0 8.1 11h-3a8 8 0 0 1 4.3-5.6zM5.1 13h3a15 15 0 0 0 1.3 5.6A8 8 0 0 1 5.1 13zm6.9 6.9c-.9-1.2-1.8-3.6-1.9-6.9h3.8c-.1 3.3-1 5.7-1.9 6.9zm2.6-1.3a15 15 0 0 0 1.3-5.6h3a8 8 0 0 1-4.3 5.6z"/></svg>
        <span>www.strideandcore.com</span>
      </li>
    </ul>
  </section>

</body>
</html>
```